Branding product image: VELMOT (Golden Papaya) in Plastic Cup (Ready to Eat)

The product is sliced Fruit in Light syrup
Flavour: VELMOT (Golden Papaya)
The temporary product name: VELMOT
I want the product design to be something 'fun', 'natural', and 'colourful'
The design concept could be anything depends on your imagination, but it must be eye catchy and attractive.
Basically, I want you to be creative in designing the logo and the overall graphic design for the label.
The measurement is 20 cm (Length) x 6,5 cm (Height)
The target customers are young and health conscious audiences (10 years - 65 years old).
Create something different. Something extraordinary.
Brief summary about the fruit:
This fruit only grows in certain part of the world. It grows in mountain area that is in tropical climate. The fruit flesh has a yellowish-golden color. It has an extraordinary taste (unlike normal papaya) and it suits very well with any dishes from cold appetizer, white/ red meat, desserts, and cocktails.
I need a packaging design for Fruit Cup productThe product is sliced Fruit in Light syrup.There will be various flavours i.e. apple, lychee, peach, papaya, etc.However, you may design the product using one sample flavour (i.e. papaya) first, as the designs of other flavours could be adjusted afterwards.The temporary product name is: RICCANAI want the product design to be something 'fun', 'natural', and 'colourful'.The design concept could be anything depends on your imagination. Basically, I want you to be creative in designing the logo and the overall graphic design for the label. - Create something different. Something extraordinary -Additional:The measurement is 20cm (Length) x 5cm (Height).The target customers are young audiences (10 years - 35 years old).The product design must stand out in the supermarket shelf.It must be eye catchy and attractive.Thank you,Jordan-PLEASE REFER TO DESIGN SAMPLE ATTACHED TO HAVE A BETTER UNDERSTANDING FOR THE PRODUCT CONCEPT- Added Wednesday, September 17, 2014
Project Deadline Extended Reason: Haven't found a good design. Added Friday, September 19, 2014
Project Deadline Extended Reason: Need more time for designers to finalize and perfect the design.Thank you,Jordan Added Monday, September 29, 2014
Project Deadline Extended Reason: I haven't found a great design yet. Added Tuesday, February 24, 2015
Reason: Getting better designs now. Still Open to new ideas while refining the latest designs from some designers.
Please do your best in submitting other great designs!

```html
<!DOCTYPE html>
<html lang="en">
<head>
<meta charset="utf-8">
<title>DOSUVEL Golden Papaya Cup Label</title>
<link rel="stylesheet" href="https://fonts.googleapis.com/css2?family=Nunito:wght@700&family=Kalam:wght@400&display=swap">
<style>
  :root {
    --bg: #e8e9eb;
    --rim: #5c2566;
    --purple-light: #a9519f;
    --purple-mid: #8a4596;
    --purple-deep: #6e3483;
    --base-band: #5a1c5e;
    --accent-green: #8fcf6a;
    --accent-lime: #b9d84a;
    --white: #ffffff;
    --papaya-skin: #f2a23a;
    --papaya-flesh: #f7b450;
    --papaya-core: #e8892a;
  }
  html, body {
    margin: 0;
    width: 1200px;
    height: 679px;
    overflow: hidden;
    background: var(--bg);
  }
  .canvas {
    position: relative;
    width: 1200px;
    height: 679px;
  }
  .cup-label {
    position: absolute;
    left: 150px;
    top: 105px;
    width: 900px;
    height: 470px;
    overflow: hidden;
    background: linear-gradient(100deg, var(--purple-light) 0%, var(--purple-mid) 45%, var(--purple-deep) 100%);
  }
  .cup-label__rim {
    position: absolute;
    left: 0; top: 0;
    width: 100%;
    height: 16px;
    background: var(--rim);
  }
  .brand {
    position: absolute;
    left: 60px;
    top: 98px;
    display: flex;
    align-items: center;
    gap: 18px;
  }
  .brand__dot {
    width: 52px;
    height: 52px;
    border-radius: 50%;
    background: var(--accent-lime);
  }
  .brand__name {
    font-family: "Nunito", sans-serif;
    font-weight: 700;
    font-size: 128px;
    line-height: 1;
    color: var(--white);
    letter-spacing: 1px;
  }
  .flavour {
    position: absolute;
    left: 127px;
    top: 272px;
    margin: 0;
    font-family: "Kalam", cursive;
    font-size: 38px;
    line-height: 46px;
    color: var(--white);
  }
  .divider {
    position: absolute;
    left: 0; top: 398px;
    width: 100%;
    height: 4px;
    background: var(--accent-green);
  }
  .base-band {
    position: absolute;
    left: 0; top: 402px;
    width: 100%;
    height: 68px;
    background: var(--base-band);
  }
  .net-weight {
    position: absolute;
    left: 150px;
    top: 424px;
    margin: 0;
    font-family: "Nunito", sans-serif;
    font-weight: 700;
    font-size: 21px;
    color: var(--white);
  }
  .fruit-visual {
    position: absolute;
    left: 395px;
    top: 258px;
    width: 320px;
    height: 185px;
  }
</style>
</head>
<body>
  <main class="canvas">
    <section class="cup-label">
      <div class="cup-label__rim"></div>
      <div class="brand">
        <span class="brand__dot"></span>
        <span class="brand__name">DOSUVEL</span>
      </div>
      <p class="flavour">Golden Papaya<br>in Light Syrup</p>
      <div class="divider"></div>
      <div class="base-band"></div>
      <p class="net-weight">Net WT 6oz(170g)</p>
      <svg class="fruit-visual" viewBox="0 0 320 185" role="img" aria-label="Photograph of two halved golden papayas">
        <defs>
          <radialGradient id="papayaTone" cx="50%" cy="50%" r="60%">
            <stop offset="0%" stop-color="var(--papaya-core)"/>
            <stop offset="55%" stop-color="var(--papaya-flesh)"/>
            <stop offset="100%" stop-color="var(--papaya-skin)"/>
          </radialGradient>
        </defs>
        <ellipse cx="115" cy="90" rx="110" ry="78" fill="url(#papayaTone)"/>
        <ellipse cx="215" cy="105" rx="100" ry="72" fill="url(#papayaTone)"/>
      </svg>
    </section>
  </main>
</body>
</html>
```